Business card

We need a business card design for our company based in Auckland , New Zealand called 'Ridge + Studio Ltd'. We provide architectural services. We would like to see designs that use the max. three colours (such as white, black, grey) The final design should communicate financial safety and growth."
Also I will provide our company logo. I would like to the logo to be embeded onto our business card.

Target Market(s)

new residential house, alteration & addition & light commericila design & drafting service

Industry/Entity Type

Architecture

Contact Information for Business Card

Company name: ridge + studio Ltd.
Name: Mark Delford
Job title: architectural designer & Design LDC
email address: mark@rplusd.co.nz
mobile number: 02 5163 2290
web site: www.rplusd.co.nz

Requirements
Must have
• My project must have..
• - embeded logo (attached company logo)
• I don't have a bigger version for our company logo, but I have one old one, so you can remove the word from it)
• - insert the attached small BKTW logo & LDC logo
• - creative, simple and clear business card.
• - Max. three colours
Nice to have
• - Here are the samples I would like to share with you: http://www.plimvora.com/blog/minimalistic-business-card-designs/
• I would like to have my business card like one of the creation.
Should not have
• TBA

```html
<!DOCTYPE html>
<html lang="en">
<head>
<meta charset="utf-8">
<title>Ridge + Studio Ltd — Business Card</title>
<link href="https://fonts.googleapis.com/css2?family=Open+Sans:wght@400;600;700&family=PT+Sans+Narrow:wght@400;700&display=swap" rel="stylesheet">
<style>
  :root {
    --backdrop: #3a3a3a;
    --ink: #000000;
    --paper: #ffffff;
    --slate: #8e9a99;
  }
  html, body {
    margin: 0;
    padding: 0;
    width: 1105px;
    height: 1200px;
    overflow: hidden;
    background: var(--backdrop);
  }
  .canvas {
    position: relative;
    width: 1105px;
    height: 1200px;
  }
  .card {
    position: absolute;
    left: 192px;
    width: 720px;
    height: 411px;
    overflow: hidden;
    font-family: "Open Sans", sans-serif;
  }
  .card--front { top: 165px; background: var(--ink); color: var(--paper); }
  .card--back { top: 623px; background: var(--slate); color: var(--paper); }

  .front-curve { position: absolute; inset: 0; }

  .holder-name {
    position: absolute; left: 42px; top: 36px; margin: 0;
    font-size: 24px; font-weight: 600; letter-spacing: 0.5px;
  }
  .holder-title {
    position: absolute; left: 42px; top: 70px; margin: 0;
    font-family: "PT Sans Narrow", sans-serif; font-size: 20px; font-weight: 400;
  }
  .company-name {
    position: absolute; left: 42px; top: 254px; margin: 0;
    font-size: 18px; font-weight: 400;
  }
  .contact-list {
    position: absolute; left: 42px; top: 290px; margin: 0; padding: 0;
    list-style: none; font-size: 17px;
  }
  .contact-list li {
    display: flex; align-items: center; height: 28px;
  }
  .contact-list svg { width: 18px; height: 18px; margin-right: 10px; flex: none; }

  .brand-mark {
    position: absolute; left: 544px; top: 206px; transform: translate(-50%, -50%);
    margin: 0; color: var(--ink); font-size: 30px; font-weight: 600; white-space: nowrap;
  }

  .badge-cert {
    position: absolute; left: 113px; top: 115px; width: 182px; height: 182px;
    border-radius: 50%; background: var(--paper);
  }
  .divider {
    position: absolute; left: 325px; top: 98px; width: 1px; height: 205px;
    background: var(--paper); opacity: 0.8;
  }
  .partner-name {
    position: absolute; left: 346px; top: 168px; margin: 0;
    font-size: 64px; font-weight: 700; letter-spacing: -1px; line-height: 1;
  }
  .back-web {
    position: absolute; left: 0; right: 0; top: 346px; margin: 0;
    text-align: center; font-size: 19px;
  }
</style>
</head>
<body>
<main class="canvas">
  <section class="card card--front">
    <svg class="front-curve" viewBox="0 0 720 411" width="720" height="411" aria-hidden="true">
      <ellipse cx="640" cy="200" rx="326" ry="268" fill="none" stroke="#ffffff" stroke-width="2.5"/>
      <ellipse cx="640" cy="200" rx="308" ry="250" fill="#ffffff"/>
    </svg>
    <h1 class="holder-name">MARK DELFORD</h1>
    <p class="holder-title">architectural designer &amp; Design LDC</p>
    <p class="company-name">ridge + studio Ltd.</p>
    <ul class="contact-list">
      <li>
        <svg viewBox="0 0 18 18"><rect x="5" y="1" width="8" height="16" rx="1.5" fill="none" stroke="#fff" stroke-width="1.6"/><rect x="7.5" y="13.5" width="3" height="1.4" fill="#fff"/></svg>
        02 5163 2290
      </li>
      <li>
        <svg viewBox="0 0 18 18"><rect x="2" y="5" width="14" height="9" fill="#fff"/><path d="M2 5 L9 10 L16 5" fill="none" stroke="#000" stroke-width="1.2"/></svg>
        mark@rplusd.co.nz
      </li>
      <li>
        <svg viewBox="0 0 18 18"><circle cx="9" cy="9" r="7" fill="#fff"/><path d="M5 6 Q8 5 9 8 Q7 10 6 13 M11 4 Q13 8 12 12" fill="none" stroke="#000" stroke-width="1.4"/></svg>
        www.rplusd.co.nz
      </li>
    </ul>
    <p class="brand-mark">ridge + studio</p>
  </section>

  <section class="card card--back">
    <div class="badge-cert" role="img" aria-label="Member certification badge"></div>
    <div class="divider"></div>
    <p class="partner-name">BKTW</p>
    <p class="back-web">www.rplusd.co.nz</p>
  </section>
</main>
</body>
</html>
```